RWT Fittings Ltd Business Cards

We need a business card with our business logo. We provide window and door installations on high-rises in west coast British Colombia, Canada.

I would like my business information and details on one side of the card, and the other side the company name with logo

Target Market(s)

General Contractors

Industry/Entity Type

Construction

Contact Information for Business Card

one side i want my company name and logo in the dark theme logo that i provided

Requirements
Must have
• Marco Peltieri, 16045518293, RWTFittings@mailbox-demo.com, 1407-5194 Linden Row Burnaby BC, V5H 2K9, Owner & Manager

```html
<!DOCTYPE html>
<html lang="en">
<head>
<meta charset="utf-8">
<title>RWT Fittings Ltd — Business Cards</title>
<link href="https://fonts.googleapis.com/css2?family=Roboto:wght@400;500;700&display=swap" rel="stylesheet">
<style>
  :root{
    --page:#232323;
    --card:#1f2026;
    --blue:#29abe2;
    --grey:#8f8f8f;
    --white:#f2f2f2;
    --photo-dark:#1c1a18;
    --photo-mid:#3a3632;
  }
  *{margin:0;padding:0;box-sizing:border-box}
  html,body{width:1200px;height:780px;overflow:hidden;background:var(--page)}
  body{font-family:"Roboto",Arial,sans-serif;position:relative}
  .card{position:absolute;top:240px;width:525px;height:300px;overflow:hidden;border-radius:3px;box-shadow:0 14px 30px rgba(0,0,0,.55)}
  .card--front{left:45px;background:var(--card)}
  .card--back{left:630px}

  .brand{position:absolute;display:flex;align-items:center;gap:12px}
  .brand__mark{width:22px;height:22px;background:var(--blue)}
  .brand__name{font-weight:700;color:var(--blue);letter-spacing:.5px}
  .card--front .brand{top:46px;left:235px}
  .card--front .brand__name{font-size:30px}

  .holder{position:absolute;left:38px;top:135px}
  .holder__name{font-size:25px;font-weight:700;line-height:1}
  .holder__first{color:var(--blue)}
  .holder__last{color:var(--grey)}
  .holder__role{margin-top:6px;font-size:14px;color:var(--white);text-align:right}

  .divider{position:absolute;left:232px;top:130px}

  .contact{position:absolute;left:275px;top:150px;list-style:none}
  .contact__item{display:flex;align-items:center;gap:10px;font-size:14.5px;color:var(--white);margin-bottom:10px}
  .contact__icon{width:15px;height:15px;flex:none}

  .address-band{position:absolute;left:0;right:0;bottom:0;height:36px;background:var(--blue);color:var(--white);font-size:15px;display:flex;align-items:center;padding-left:34px}

  .backdrop{position:absolute;inset:0;background:radial-gradient(ellipse at 70% 55%,var(--photo-mid),var(--photo-dark) 75%)}
  .card--back .brand{left:50%;top:50%;transform:translate(-50%,-50%)}
  .card--back .brand__name{font-size:34px}
</style>
</head>
<body>
  <section class="card card--front" aria-label="Business card, contact side">
    <div class="brand">
      <span class="brand__mark"></span>
      <span class="brand__name">RWT Fittings Ltd</span>
    </div>

    <div class="holder">
      <p class="holder__name"><span class="holder__first">Marco</span> <span class="holder__last">Peltieri</span></p>
      <p class="holder__role">Owner &amp; Manager</p>
    </div>

    <svg class="divider" width="30" height="95" viewBox="0 0 30 95" aria-hidden="true">
      <line x1="28" y1="0" x2="2" y2="95" stroke="#cfcfcf" stroke-width="1"/>
    </svg>

    <ul class="contact">
      <li class="contact__item">
        <svg class="contact__icon" viewBox="0 0 24 24" aria-hidden="true"><path fill="#29abe2" d="M6.6 10.8a15 15 0 0 0 6.6 6.6l2.2-2.2a1 1 0 0 1 1-.25 11.4 11.4 0 0 0 3.6.57 1 1 0 0 1 1 1V20a1 1 0 0 1-1 1A17 17 0 0 1 3 4a1 1 0 0 1 1-1h3.5a1 1 0 0 1 1 1c0 1.25.2 2.45.57 3.6a1 1 0 0 1-.25 1z"/></svg>
        1604 551 8293
      </li>
      <li class="contact__item">
        <svg class="contact__icon" viewBox="0 0 24 24" aria-hidden="true"><rect x="2" y="5" width="20" height="14" rx="1.5" fill="#29abe2"/><path d="M3 6l9 7 9-7" fill="none" stroke="#1f2026" stroke-width="1.8"/></svg>
        RWTFittings@mailbox-demo.com
      </li>
    </ul>

    <div class="address-band">1407-5194 Linden Row Burnaby BC, V5H 2K9</div>
  </section>

  <section class="card card--back" aria-label="Business card, brand side">
    <div class="backdrop" role="img" aria-label="Dim interior photograph of an office with plants"></div>
    <div class="brand">
      <span class="brand__mark"></span>
      <span class="brand__name">RWT Fittings Ltd</span>
    </div>
  </section>
</body>
</html>
```